Business Card Design Project

We need a business card for a new technology services company. We develop software and implement software packages for our business customers and although we will begin with just one or two service offerings, our service offerings will expand over time. Our name comes from the an author, KL Barrow, and his "idea" was that opportunity should be based on ability and achievement, not on social status.

We would like to see a design that is standard in its size and shape, but stands apart in its dramatic color contrasts. The card should not use too many colors - the colors used in the background should highlight the brilliant blues of the logo (see attachment) to dramatic effect. The background should not be white.

If necessary, you can change the color of the words "KL Barrow", but not the word "Idea".

Card size should be U.S. standard 2 inches by 3.5 inches and provide for 1/8 inch bleed area on each side.

We need a design for both sides of the business card, one side communicating the company logo and contact information, the other side being purely graphical, incorporating the logo but no other information.

Contact Information Required:
Kate Brook
KateBrook@klbarrowvista.com
614-387-2259

Target Market(s)

Business executives

Industry/Entity Type

Software

Requirements
Must have
• It must have the full company logo on one side, and at least the graphic element of the logo on the other. Either that or the full logo on both.
Nice to have
• It would be nice to have a design that could work without needing two different textures. For example, it would be nice if the entire card could be shiny, not just parts of the card.

It would also be nice if texture is something we could add later.
Should not have
• The card should not use the color green.

```html
<!DOCTYPE html>
<html lang="en">
<head>
<meta charset="utf-8">
<title>KL Barrow Vista – Business Card</title>
<link rel="stylesheet" href="https://fonts.googleapis.com/css2?family=Open+Sans:wght@400;700&display=swap">
<style>
  :root {
    --stage: #e9e7e3;
    --card-dark: #1d1d1f;
    --card-mid: #2c2c2e;
    --card-sheen: #3a3a3d;
    --brand-blue: #1a9be0;
    --brand-blue-faint: rgba(26, 155, 224, 0.3);
    --text-light: #d9dadb;
    --text-white: #ffffff;
    --rule-gray: #8c8d90;
  }
  * { box-sizing: border-box; margin: 0; padding: 0; }
  html, body {
    width: 1200px; height: 720px; overflow: hidden;
    background: var(--stage);
    font-family: "Open Sans", Arial, sans-serif;
  }
  .canvas {
    width: 1200px; height: 720px;
    display: flex; align-items: center; justify-content: center; gap: 48px;
  }
  .card {
    position: relative;
    width: 530px; height: 303px;
    border-radius: 4px;
    overflow: hidden;
    background:
      radial-gradient(ellipse at 55% 15%, var(--card-sheen) 0%, transparent 60%),
      linear-gradient(180deg, var(--card-mid) 0%, var(--card-dark) 100%);
    box-shadow: 0 10px 26px rgba(0,0,0,0.22);
  }

  /* Company name */
  .company-name {
    position: absolute;
    display: flex; align-items: center; gap: 16px;
  }
  .company-name-text {
    font-weight: 400;
    color: var(--text-light);
    text-transform: uppercase;
    letter-spacing: 4px;
    white-space: nowrap;
  }
  .company-square {
    flex: none;
    background: var(--brand-blue-faint);
  }

  /* Front: name + contact */
  .card-front .company-name { left: 40px; top: 74px; }
  .card-front .company-name-text { font-size: 28px; }
  .card-front .company-square { width: 20px; height: 20px; }

  .name-band {
    position: absolute; left: 0; right: 0; top: 138px;
    border-top: 2px solid var(--rule-gray);
    border-bottom: 2px solid var(--rule-gray);
    padding: 3px 0;
  }
  .name-band-fill {
    background: var(--brand-blue);
    height: 40px;
    display: flex; align-items: center; justify-content: center;
  }
  .person-name {
    font-weight: 700; font-size: 18px; letter-spacing: 1px;
    color: var(--text-white); text-transform: uppercase;
  }
  .contact-row {
    position: absolute; left: 0; right: 0; top: 222px;
    display: flex; justify-content: center; gap: 34px;
    font-size: 14px; color: var(--text-white);
  }
  .contact-item { display: flex; align-items: center; gap: 7px; }
  .contact-icon { width: 14px; height: 14px; fill: var(--brand-blue); }

  /* Back: company name only */
  .card-back .company-name {
    left: 0; right: 0; top: 0; bottom: 0;
    justify-content: center;
  }
  .card-back .company-name-text { font-size: 32px; }
  .card-back .company-square { width: 26px; height: 26px; }
</style>
</head>
<body>
<main class="canvas">

  <section class="card card-front" aria-label="Business card front">
    <div class="company-name">
      <span class="company-name-text">KL Barrow Vista</span>
      <span class="company-square"></span>
    </div>

    <div class="name-band">
      <div class="name-band-fill">
        <span class="person-name">Kate Brook</span>
      </div>
    </div>

    <div class="contact-row">
      <span class="contact-item">
        <svg class="contact-icon" viewBox="0 0 24 24" aria-hidden="true">
          <path d="M6.6 10.8a15.1 15.1 0 0 0 6.6 6.6l2.2-2.2a1 1 0 0 1 1-.25 11.4 11.4 0 0 0 3.6.57 1 1 0 0 1 1 1V20a1 1 0 0 1-1 1A17 17 0 0 1 3 4a1 1 0 0 1 1-1h3.5a1 1 0 0 1 1 1c0 1.25.2 2.45.57 3.57a1 1 0 0 1-.25 1z"/>
        </svg>
        614-387-2259
      </span>
      <span class="contact-item">
        <svg class="contact-icon" viewBox="0 0 24 24" aria-hidden="true">
          <path d="M3 5h18a1 1 0 0 1 1 1v12a1 1 0 0 1-1 1H3a1 1 0 0 1-1-1V6a1 1 0 0 1 1-1zm1 2.3V17h16V7.3l-8 5.2z"/>
        </svg>
        KateBrook@klbarrowvista.com
      </span>
    </div>
  </section>

  <section class="card card-back" aria-label="Business card back">
    <div class="company-name">
      <span class="company-name-text">KL Barrow Vista</span>
      <span class="company-square"></span>
    </div>
  </section>

</main>
</body>
</html>
```